Health Information/Education Logo Design

We need a logo design for a new company based in Atlanta called Meadowlark Health. The program is about patient empowerment. We provide health information and education on how to get healthy, stay healthy, and how to be proactive in your care. We also provide medication and injection training to help patients feel their best and to ensure successful therapy outcomes.
We like the colors yellow, pink, teal and purple and would like to see some or all of these colors in the designs. The final design should communicate caring, considerate, compassionate information, education and training services
Industry/Entity Type
Education
Contact Information for Business Card
Meadowlark Health
Danielle Ashworth RN, MSN, MHA
Nurse Educator
404.555.0186 cell
404.555.0142 fax

```html
<!DOCTYPE html>
<html lang="en">
<head>
<meta charset="utf-8">
<title>Meadowlark Health — Business Card</title>
<link rel="stylesheet" href="https://fonts.googleapis.com/css2?family=Open+Sans:wght@400;600&display=swap">
<style>
  :root {
    --bg: #ecebee;
    --card: #ffffff;
    --purple: #5b45a0;
    --pink: #e0338f;
    --ink: #333333;
    --shadow: rgba(40, 30, 60, 0.18);
  }
  * { margin: 0; padding: 0; box-sizing: border-box; }
  html, body {
    width: 1200px; height: 891px; overflow: hidden;
    background: var(--bg);
    font-family: "Open Sans", Arial, sans-serif;
  }
  .stage { position: relative; width: 1200px; height: 891px; }
  .card {
    position: absolute;
    width: 560px; height: 320px;
    background: var(--card);
    box-shadow: 0 10px 28px var(--shadow);
    overflow: hidden;
  }
  .card--front { left: 90px; top: 110px; }
  .card--back { left: 550px; top: 461px; }

  .brand { display: flex; align-items: center; gap: 12px; position: absolute; }
  .brand__dot { width: 22px; height: 22px; border-radius: 50%; background: var(--pink); flex: none; }
  .brand__name { color: var(--purple); font-weight: 600; letter-spacing: 0.5px; white-space: nowrap; }

  .card--front .brand { left: 50%; top: 50%; transform: translate(-50%, -50%); }
  .card--front .brand__name { font-size: 34px; }

  .card--back .brand { left: 36px; top: 150px; }
  .card--back .brand__dot { width: 16px; height: 16px; }
  .card--back .brand__name { font-size: 21px; }

  .contact { position: absolute; left: 318px; top: 40px; }
  .contact__name { color: var(--purple); font-size: 17px; }
  .contact__role { color: var(--pink); font-size: 11px; margin-top: 3px; }
  .contact__lines { margin-top: 44px; font-size: 11.5px; color: var(--ink); line-height: 1.75; }
  .contact__label { display: inline-block; width: 18px; }

  .footer-band { position: absolute; left: 0; right: 0; bottom: 18px; }
  .footer-band__rule { height: 3px; background: var(--pink); }
  .footer-band__bar {
    height: 50px; margin: 4px 0;
    background: var(--purple);
    color: #ffffff;
    font-size: 19px; letter-spacing: 8px;
    display: flex; align-items: center; justify-content: center;
  }
</style>
</head>
<body>
<main class="stage">
  <section class="card card--front" aria-label="Business card front">
    <div class="brand">
      <span class="brand__dot"></span>
      <span class="brand__name">Meadowlark Health</span>
    </div>
  </section>

  <section class="card card--back" aria-label="Business card back">
    <div class="brand">
      <span class="brand__dot"></span>
      <span class="brand__name">Meadowlark Health</span>
    </div>
    <div class="contact">
      <p class="contact__name">Danielle Ashworth RN, MSN</p>
      <p class="contact__role">MHA Nurse Educator</p>
      <p class="contact__lines">
        <span class="contact__label">M</span>: 404.555.0186<br>
        <span class="contact__label">F</span>: 404.555.0142
      </p>
    </div>
    <div class="footer-band">
      <div class="footer-band__rule"></div>
      <div class="footer-band__bar">www.meadowlark-health.com.au</div>
      <div class="footer-band__rule"></div>
    </div>
  </section>
</main>
</body>
</html>
```